design a construction company business card

Design business card around our logo. Card must have all the typical info: name, title, address, phone, email, business name, etc. Somewhere on the card I would like to see our motto "Grounded in trust... Driven by dedication." Consider adding a splash of bright orange to the card to complement the blues and silvers/grays in the logo. We are open to metallic inks, textures, etc. We would like to see options on both light and dark backgrounds. The font in the logo is Euro Technic Extended Regular.

```html
<!DOCTYPE html>
<html lang="en">
<head>
<meta charset="utf-8">
<title>Halden Contracting – Business Card</title>
<link href="https://fonts.googleapis.com/css2?family=Michroma&family=Orbitron:wght@700&family=Montserrat:wght@400;500&display=swap" rel="stylesheet">
<style>
  :root {
    --backdrop: #3c3d41;
    --card-dark: #1f2022;
    --card-light: #ffffff;
    --brand-blue: #1d4fb8;
    --motto-blue: #1f73d6;
    --text-grey: #4a4a4e;
    --icon-blue: #2a63c9;
  }
  * { margin: 0; padding: 0; box-sizing: border-box; }
  html, body { width: 1200px; height: 1000px; overflow: hidden; }
  body {
    background: var(--backdrop);
    position: relative;
    font-family: "Montserrat", sans-serif;
  }
  .card {
    position: absolute;
    width: 760px;
    height: 420px;
    border-radius: 28px;
  }
  .card-front { left: 330px; top: 50px; background: var(--card-dark); }
  .card-back  { left: 120px; top: 530px; background: var(--card-light); }

  .wordmark {
    position: absolute;
    display: flex;
    align-items: center;
    gap: 14px;
    font-family: "Michroma", sans-serif;
    color: var(--brand-blue);
    line-height: 1.15;
  }
  .wordmark-square { width: 22px; height: 22px; background: var(--brand-blue); flex: none; }
  .wordmark-name { font-size: 40px; letter-spacing: 2px; }
  .wordmark-sub { display: block; font-size: 15px; letter-spacing: 3px; }

  .card-front .wordmark { left: 200px; top: 120px; }
  .motto {
    position: absolute;
    left: 0; right: 0; top: 290px;
    text-align: center;
    font-family: "Orbitron", sans-serif;
    font-weight: 700;
    font-size: 15px;
    letter-spacing: 1px;
    color: var(--motto-blue);
    text-transform: uppercase;
  }

  .card-back .wordmark { left: 430px; top: 100px; }
  .card-back .wordmark-name { font-size: 34px; }
  .card-back .wordmark-sub { font-size: 13px; }

  .person { position: absolute; left: 70px; top: 90px; }
  .person-name {
    font-family: "Orbitron", sans-serif;
    font-weight: 700;
    font-size: 20px;
    color: var(--brand-blue);
  }
  .person-title { font-size: 13px; color: var(--text-grey); margin-top: 4px; }

  .contact { position: absolute; left: 70px; top: 255px; font-size: 15px; color: var(--text-grey); }
  .contact-line { display: flex; align-items: center; gap: 8px; height: 26px; }
  .contact-web { position: absolute; left: 330px; top: 320px; font-size: 15px; color: var(--text-grey); display: flex; align-items: center; gap: 8px; height: 26px; }
  .icon { width: 13px; height: 13px; flex: none; }
</style>
</head>
<body>

  <section class="card card-front">
    <div class="wordmark">
      <span class="wordmark-square"></span>
      <span class="wordmark-name">HALDEN<span class="wordmark-sub">CONTRACTING, INC.</span></span>
    </div>
    <p class="motto">Grounded in trust... Driven by dedication.</p>
  </section>

  <section class="card card-back">
    <div class="person">
      <p class="person-name">Marcus Lyle</p>
      <p class="person-title">Managing Director</p>
    </div>

    <div class="wordmark">
      <span class="wordmark-square"></span>
      <span class="wordmark-name">HALDEN<span class="wordmark-sub">CONTRACTING, INC.</span></span>
    </div>

    <div class="contact">
      <p class="contact-line">48 Harbor Street Eastfield NY 10021</p>
      <p class="contact-line">
        <svg class="icon" viewBox="0 0 16 16" aria-hidden="true"><path fill="var(--icon-blue)" d="M3 1l3 3-1.5 2a9 9 0 005 5L11.5 9.5l3 3L13 15C7 15 1 9 1 3z"/></svg>
        555.014.2200
      </p>
      <p class="contact-line">
        <svg class="icon" viewBox="0 0 16 16" aria-hidden="true"><rect x="1" y="3" width="14" height="10" rx="1.5" fill="var(--icon-blue)"/><path d="M2 4l6 5 6-5" stroke="#fff" stroke-width="1.4" fill="none"/></svg>
        marcus@haldenbuild.com
      </p>
    </div>
    <p class="contact-web">
      <svg class="icon" viewBox="0 0 16 16" aria-hidden="true"><circle cx="8" cy="8" r="7" fill="var(--icon-blue)"/><path d="M1 8h14M8 1c3 3 3 11 0 14M8 1c-3 3-3 11 0 14" stroke="#fff" stroke-width="1" fill="none"/></svg>
      www.haldenbuild.com
    </p>
  </section>

</body>
</html>
```